Design a large parking banner – mandatory ticket validation in the shop

Banner Size:
548 cm (width) x 154 cm (height)
Note: The banner will be placed in a metal frame at our parking lot entrance, fully visible to every incoming truck driver. The message must be easy to read from a distance.
Goal of the Banner:
To inform all truck drivers that they must validate their entry ticket inside the shop, even if they are parking for a short time.
The message must be displayed in multiple languages for international drivers.
Mandatory Content:
Main message – in multiple languages (clearly separated or stacked):
Dutch (NL): Vergeet je ticket niet te valideren in de shop – verplicht, ook bij kort parkeren!
French (FR): N'oubliez pas de valider votre ticket à la boutique – obligatoire, même pour un court arrêt !
English (EN): Don't forget to validate your entry ticket in the shop – mandatory, even for short stops!
German (DE): Vergessen Sie nicht, Ihr Einfahrticket im Shop zu entwerten – Pflicht, auch bei kurzem Parken!
Polish (PL): Nie zapomnij zatwierdzić biletu w sklepie – obowiązkowe, nawet przy krótkim postoju!
Romanian (RO): Nu uitați să validați biletul în magazin – obligatoriu, chiar și pentru opriri scurte!
You can include more languages if space allows, but these are essential.
Opening Hours Block (in one section below):
Shop Opening Hours
Mon – Fri: 05:30 – 22:00
Sat & Sun: 08:00 – 22:00
Style & Branding:
The design must match the visual identity of Haulport 41Ter
Please refer to the attached photos of existing parking signage for guidance on colors, typography, and layout style
Our logo (attached) must be clearly visible and professionally integrated
Feel free to use icons or pictograms to visually support the message (e.g., ticket, truck, arrow)
Readability is key – large, bold text and high contrast colors that are visible from a distance
Target Audience:
International truck drivers – people who need fast, clear communication. Not everyone speaks the local language, so visual clarity and multilingual messaging are critical.
File Requirements:
Print-ready file (PDF or EPS) – 300 dpi at 1:10 scale
Include 5 cm bleed on all sides
Provide open source files if possible (AI or PSD)

```html
<!DOCTYPE html>
<html lang="en">
<head>
<meta charset="utf-8">
<title>Haulport 41Ter – Ticket Validation Banner</title>
<link rel="stylesheet" href="https://fonts.googleapis.com/css2?family=Bebas+Neue&display=swap">
<style>
  :root {
    --navy: #252358;
    --red: #d3161d;
    --blue: #1b83c9;
    --white: #ffffff;
    --backdrop: #eef1f4;
    --display: "Bebas Neue", "Arial Narrow", sans-serif;
  }
  * { margin: 0; padding: 0; box-sizing: border-box; }
  html, body {
    width: 1135px;
    height: 1200px;
    overflow: hidden;
    background: var(--backdrop);
  }
  .canvas {
    position: relative;
    width: 1135px;
    height: 1200px;
  }
  .banner {
    position: absolute;
    left: 0;
    top: 432px;
    width: 1135px;
    height: 336px;
    background: var(--navy);
    overflow: hidden;
    font-family: var(--display);
    color: var(--white);
  }
  .brand {
    position: absolute;
    left: 28px;
    top: 112px;
    width: 300px;
  }
  .brand-name {
    font-size: 56px;
    line-height: 1;
    letter-spacing: 0.5px;
    color: var(--white);
    white-space: nowrap;
  }
  .brand-rule {
    margin-top: 18px;
    width: 172px;
    height: 5px;
    background: var(--red);
  }
  .messages {
    position: absolute;
    left: 357px;
    top: 22px;
    list-style: none;
  }
  .message {
    position: relative;
    height: 41px;
    padding-top: 6px;
    font-size: 19.5px;
    line-height: 22px;
    white-space: nowrap;
  }
  .message::after {
    content: "";
    position: absolute;
    left: 0;
    top: 30px;
    width: 760px;
    height: 2px;
    background: linear-gradient(90deg, var(--red) 0%, var(--red) 55%, rgba(211,22,29,0) 100%);
  }
  .message:last-child::after { display: none; }
  .hours-band {
    position: absolute;
    left: 0;
    top: 271px;
    width: 1135px;
    height: 65px;
  }
  .hours-band svg { position: absolute; inset: 0; }
  .hours-label,
  .hours-slot {
    position: absolute;
    top: 10px;
    font-size: 32px;
    line-height: 50px;
    white-space: nowrap;
    color: var(--white);
  }
  .hours-label { left: 49px; }
  .hours-weekdays { left: 446px; }
  .hours-weekend { left: 824px; }
</style>
</head>
<body>
<div class="canvas">
  <section class="banner" aria-label="Ticket validation parking banner">
    <div class="brand">
      <div class="brand-name">Haulport 41Ter</div>
      <div class="brand-rule"></div>
    </div>

    <ul class="messages">
      <li class="message" lang="nl">VERGEET JE TICKET NIET TE VALIDEREN IN DE SHOP – VERPLICHT, OOK BIJ KORT PARKEREN!</li>
      <li class="message" lang="fr">N'OUBLIEZ PAS DE VALIDER VOTRE TICKET À LA BOUTIQUE – OBLIGATOIRE, MÊME POUR UN COURT ARRÊT !</li>
      <li class="message" lang="en">DON'T FORGET TO VALIDATE YOUR ENTRY TICKET IN THE SHOP – MANDATORY, EVEN FOR SHORT STOPS!</li>
      <li class="message" lang="de">VERGESSEN SIE NICHT, IHR EINFAHRTICKET IM SHOP ZU ENTWERTEN – PFLICHT, AUCH BEI KURZEM PARKEN!</li>
      <li class="message" lang="pl">NIE ZAPOMNIJ ZATWIERDZIĆ BILETU W SKLEPIE – OBOWIĄZKOWE, NAWET PRZY KRÓTKIM POSTOJU!</li>
      <li class="message" lang="ro">NU UITAȚI SĂ VALIDAȚI BILETUL ÎN MAGAZIN – OBLIGATORIU, CHIAR ȘI PENTRU OPRIRI SCURTE!</li>
    </ul>

    <div class="hours-band">
      <svg width="1135" height="65" viewBox="0 0 1135 65" aria-hidden="true">
        <rect x="0" y="0" width="1135" height="65" fill="var(--red)"/>
        <rect x="0" y="0" width="1135" height="6" fill="var(--blue)"/>
        <polygon points="0,6 397,6 364,65 0,65" fill="var(--blue)"/>
        <polygon points="772,6 794,6 761,65 739,65" fill="var(--white)"/>
      </svg>
      <div class="hours-label">SHOP OPENING HOURS</div>
      <div class="hours-slot hours-weekdays">MON – FRI: 05:30 – 22:00</div>
      <div class="hours-slot hours-weekend">SAT &amp; SUN: 08:00 – 22:00</div>
    </div>
  </section>
</div>
</body>
</html>
```